Employment Agency Website Design

We are working with an employment agency in California.

Some sites to use for content/competitors and inspiration:

https://www.pinecrestjobs.com/us/en
https://www.velmorusa.com
https://www.dravenworks.us
https://www.quillora.com/en
https://www.tomvalusa.com
https://www.fernstaffing.com

Thank you for taking the time to consider designing a website for us. We are web developers based in Stockton, CA, USA. Most of our projects go through the same process. Understanding this process may help you win a project with us. We custom-code all of our websites in-house. We don’t have any requirements as to what tools you use for your design, but we prefer Figma files. For any design that we label as four-stars, we send it to the client for review. The client picks the final design they want us to use. Once we complete this process, we will continue to show additional clients all the four-star sites and purchase them later. Your designs will have multiple chances to sell. For better chances of success, we ask that you follow these guidelines.

IMAGES:
If you use any images or icons in the design, we ask that you have a link to the asset so we can purchase the image/icon. Most of the designs we submit do not have the customer’s images on them unless they have some great images. Be creative; show us the feeling you are trying to portray with your image choices. Use any royalty-free site you choose. We subscribe to Adobe and mainly use their images, but we can purchase images outside of Adobe. PLEASE NOTE: we will not submit designs to clients with watermarks on the images.

FONTS:
We ask that you identify the fonts used in the design. This can be done in a message if you want. We typically use Google Fonts and Adobe Fonts.

CONTENT:
We're always open to different content and ideas. We often submit designs with stock images so the client can see our vision. We typically take pictures after the website launch to use their images with our vision. Lorem Ipsum is fine for paragraphs, but we ask that you write the headers in correct English. We want to be able to show the vision and identify the sections of the website.

INSPIRATION:
We typically add a couple of links in the brief of websites we like to help you get started in your design.

REVISIONS:
We do not often ask for revisions of the designs unless we see something in the design that may not appeal to the client. If there are slight changes that we want to make, we do that in the development process.

FEEDBACK:
We rarely give feedback on designs during the design process. We are working on many website projects and do not have the time to provide feedback. We usually respond if your request is well thought out and asks specific questions, but a note asking “feedback, please” usually goes unanswered.

```html
<!DOCTYPE html>
<html lang="en">
<head>
<meta charset="utf-8">
<title>Stridework — Connecting Talent to Opportunity</title>
<link href="https://fonts.googleapis.com/css2?family=Lato:wght@400;700&display=swap" rel="stylesheet">
<style>
:root{
  --red:#c41e2e;
  --ink:#1a1a1a;
  --muted:#7a7a7a;
  --page:#f7f7f7;
  --line:#cfcfcf;
  --footer:#e9e9e9;
  --white:#ffffff;
}
*{box-sizing:border-box;margin:0;padding:0}
html,body{width:1200px;height:3118px;overflow:hidden}
body{position:relative;background:var(--page);font-family:'Lato',sans-serif;color:var(--ink)}
.abs{position:absolute}
a{color:inherit;text-decoration:none}

/* hero */
.hero{left:0;top:0;width:1200px;height:750px;background:linear-gradient(180deg,#4a4a48 0%,#3a3937 40%,#262523 100%)}
.hero-photo{left:0;top:0;width:1200px;height:750px;background:radial-gradient(ellipse at 50% 30%,rgba(200,200,195,.35),rgba(0,0,0,0) 60%),linear-gradient(180deg,#595955 0%,#3d3c39 50%,#1e1d1b 100%)}
.nav{left:171px;top:27px;width:858px;height:86px;background:var(--white);display:flex;align-items:center;padding:0 27px;font-size:13px}
.brand{display:flex;align-items:center;gap:7px;font-size:18px;font-weight:700;color:var(--red);margin-right:33px}
.brand-mark{width:16px;height:16px;background:var(--red);border-radius:50%}
.nav-links{display:flex;gap:20px}
.nav-links .active{text-decoration:underline;text-underline-offset:4px}
.account{margin-left:auto;display:flex;align-items:center;gap:7px}
.account .sep{width:1px;height:18px;background:var(--ink)}
.hero-title{left:0;top:255px;width:1200px;text-align:center;color:var(--white);font-size:56px;font-weight:700}
.btn{display:flex;align-items:center;justify-content:center;font-size:17px}
.btn-red{background:var(--red);color:var(--white)}
.btn-ghost{border:1px solid var(--white);color:var(--white)}
.search-band{left:0;top:463px;width:1200px;height:262px;background:rgba(20,20,20,.55)}
.search-label{left:103px;top:515px;color:var(--white);font-size:28px;font-weight:700}
.field{background:var(--white);height:46px;top:562px;display:flex;align-items:center;padding-left:14px;font-size:17px}
.filter{right:103px;top:620px;color:var(--white);font-size:17px;display:flex;align-items:center;gap:8px}

/* jobs */
.tabs{left:0;top:838px;width:1200px;display:flex;justify-content:center;gap:27px;font-size:17px;color:var(--muted)}
.tabs .on{color:var(--ink);border-bottom:2px solid var(--red);padding:0 7px 6px}
.card{width:332px;height:100px;border:1px solid var(--line);background:var(--white);padding:14px 13px}
.card h3{font-size:21px;font-weight:400}
.card p{font-size:13px;color:var(--muted);margin-top:6px}
.card .more{position:absolute;right:13px;bottom:12px;font-size:11px;color:var(--red);display:flex;align-items:center;gap:8px}
.card .more i{width:13px;height:13px;background:#d9d9d9;display:block}

/* feature blocks */
.feature-title{font-size:31px;font-weight:700;line-height:1.15}
.feature-text{font-size:17px;line-height:1.4}
.photo-a{left:694px;top:1474px;width:422px;height:438px;background:linear-gradient(135deg,#5b6b62 0%,#a9b5b1 45%,#e6e3dc 100%)}
.photo-b{left:83px;top:2079px;width:422px;height:438px;background:linear-gradient(135deg,#8ea4c4 0%,#c8d2df 40%,#2a2a2c 100%)}

/* talent band */
.talent{left:0;top:2600px;width:1200px;height:285px;background:var(--red);color:var(--white)}

/* footer */
.footer{left:0;top:2885px;width:1200px;height:233px;background:var(--footer)}
.fcol h4{font-size:13px;font-weight:700;color:var(--red);margin-bottom:18px}
.fcol li{list-style:none;font-size:13px;margin-bottom:15px}
.fcol li::before{content:"›";color:var(--red);margin-right:12px}
.social{display:flex;gap:16px;align-items:center}
.social span{width:22px;height:22px;border-radius:50%;background:var(--ink);display:block}
</style>
</head>
<body>

<header>
  <div class="abs hero"></div>
  <div class="abs hero-photo" role="img" aria-label="Open-plan office interior with desks, pendant lamps and potted plants"></div>

  <nav class="abs nav">
    <a class="brand" href="#"><span class="brand-mark"></span>Stridework</a>
    <div class="nav-links">
      <a class="active" href="#">Job Opportunities</a>
      <a href="#">Location</a>
      <a href="#">About Us</a>
      <a href="#">For Employers</a>
      <a href="#">Resources</a>
    </div>
    <div class="account">
      <svg width="14" height="14" viewBox="0 0 14 14"><circle cx="7" cy="4" r="3.2" fill="#c41e2e"/><path d="M1 14c0-4 3-6 6-6s6 2 6 6z" fill="#c41e2e"/></svg>
      <a href="#">Login</a><span class="sep"></span><a href="#">Create An Account</a>
    </div>
  </nav>

  <h1 class="abs hero-title">Connecting Talent to Opportunity</h1>
  <a class="abs btn btn-red" style="left:445px;top:348px;width:138px;height:46px" href="#">Explore Job</a>
  <a class="abs btn btn-ghost" style="left:597px;top:348px;width:158px;height:46px" href="#">Login/Sign Up</a>

  <div class="abs search-band"></div>
  <h2 class="abs search-label">I’m Looking For...</h2>
  <div class="abs field" style="left:103px;width:417px">Job Title, Company, Keyword</div>
  <div class="abs field" style="left:534px;width:416px">Location</div>
  <a class="abs btn btn-red" style="left:964px;top:562px;width:133px;height:46px" href="#">Search Job</a>
  <div class="abs filter">Add Filter
    <svg width="18" height="16" viewBox="0 0 18 16" fill="none" stroke="#fff" stroke-width="1.6"><path d="M1 3h16M1 8h16M1 13h16"/><circle cx="12" cy="3" r="2" fill="#3a3a3a"/><circle cx="6" cy="8" r="2" fill="#3a3a3a"/><circle cx="11" cy="13" r="2" fill="#3a3a3a"/></svg>
  </div>
</header>

<main>
  <div class="abs tabs">
    <span class="on">Recently Added</span><span>Jobs by Category</span><span>Jobs by Company</span>
  </div>

  <section>
    <div class="abs card" style="left:83px;top:894px"><h3>Job Title</h3><p>Company Name</p><span class="more">More details<i></i></span></div>
    <div class="abs card" style="left:434px;top:894px"><h3>Job Title</h3><p>Company Name</p><span class="more">More details<i></i></span></div>
    <div class="abs card" style="left:785px;top:894px"><h3>Job Title</h3><p>Company Name</p><span class="more">More details<i></i></span></div>
    <div class="abs card" style="left:83px;top:1014px"><h3>Job Title</h3><p>Company Name</p><span class="more">More details<i></i></span></div>
    <div class="abs card" style="left:434px;top:1014px"><h3>Job Title</h3><p>Company Name</p><span class="more">More details<i></i></span></div>
    <div class="abs card" style="left:785px;top:1014px"><h3>Job Title</h3><p>Company Name</p><span class="more">More details<i></i></span></div>
    <div class="abs card" style="left:83px;top:1134px"><h3>Job Title</h3><p>Company Name</p><span class="more">More details<i></i></span></div>
    <div class="abs card" style="left:434px;top:1134px"><h3>Job Title</h3><p>Company Name</p><span class="more">More details<i></i></span></div>
    <div class="abs card" style="left:785px;top:1134px"><h3>Job Title</h3><p>Company Name</p><span class="more">More details<i></i></span></div>
    <a class="abs btn btn-red" style="left:508px;top:1261px;width:184px;height:46px" href="#">More Jobs</a>
  </section>

  <section>
    <h2 class="abs feature-title" style="left:83px;top:1550px;width:520px">Begin your journey to a new career with Stridework</h2>
    <p class="abs feature-text" style="left:83px;top:1648px;width:520px">With thousands of job opportunities spanning the nation, we're dedicated to connecting you with the perfect job, whether it's a remote position or something closer to home. Our extensive selection includes work-from-home options, traditional office roles, and everything in between.</p>
    <a class="abs btn btn-red" style="left:83px;top:1790px;width:199px;height:46px" href="#">Explore Jobs</a>
    <div class="abs photo-a" role="img" aria-label="White coffee mug on a desk beside a laptop and plant leaves"></div>
  </section>

  <section>
    <div class="abs photo-b" role="img" aria-label="Two professionals shaking hands, one holding a folder"></div>
    <h2 class="abs feature-title" style="left:606px;top:2148px;width:510px">Find Your Perfect Career Fit</h2>
    <p class="abs feature-text" style="left:606px;top:2212px;width:512px">By learning about your unique qualities, dreams, and expectations, we can match you with a job that aligns with your personality and goals. Share your story with us, and we'll guide you towards fulfilling employment opportunities that resonate with your true self. Whether it's today, tomorrow, or as your career evolves, we're dedicated to helping you harness your potential and find work that brings you genuine satisfaction.</p>
    <a class="abs btn btn-red" style="left:606px;top:2400px;width:199px;height:46px" href="#">Explore Jobs</a>
  </section>

  <section class="abs talent">
    <h2 class="abs" style="left:83px;top:82px;font-size:30px;font-weight:700">Looking For A Talent?</h2>
    <p class="abs feature-text" style="left:83px;top:130px;width:610px">Whether it's a demand for full-time roles, seasonal surges, project-specific requirements, or covering extended leaves, we have the ideal candidates ready to hit the ground running.</p>
    <a class="abs btn" style="left:880px;top:118px;width:236px;height:46px;background:#fff;color:var(--ink)" href="#">For Employers&nbsp;&nbsp;&nbsp;›</a>
  </section>
</main>

<footer class="abs footer">
  <a class="abs brand" style="left:88px;top:52px;font-size:21px" href="#"><span class="brand-mark" style="width:20px;height:20px"></span>Stridework</a>
  <p class="abs" style="left:83px;top:118px;width:340px;font-size:12px;line-height:1.35">Lorem ipsum dolor sit amet consectetur. Aliquam sit nec sollicitudin nulla consectetur cursus sit. Nam sagittis.</p>
  <div class="abs social" style="left:83px;top:156px">
    <span style="width:auto;height:auto;background:none;border-radius:0;color:var(--red);font-size:13px;font-weight:700">Follow Us</span>
    <span aria-label="Social profile"></span><span aria-label="Social profile"></span><span aria-label="Social profile"></span>
  </div>
  <div class="abs fcol" style="left:511px;top:54px"><h4>Company</h4><ul><li>About Us</li><li>Contact Us</li><li>Blog</li></ul></div>
  <div class="abs fcol" style="left:648px;top:54px"><h4>For Jobs</h4><ul><li>Browse Categories</li><li>Browse Jobs</li><li>Job Details</li></ul></div>
  <div class="abs fcol" style="left:831px;top:54px"><h4>For Employers</h4><ul><li>Find Candidates</li><li>Candidates Details</li></ul></div>
  <div class="abs fcol" style="left:1014px;top:54px"><h4>Support</h4><ul><li>FAQs</li><li>Help Center</li><li>Privacy Policy</li></ul></div>
</footer>

</body>
</html>
```